Beacon Advisory Website

I currently have a website www.beaconadvisoryinc.com. We are a IT Consulting Company. Our website will pretty much tell out our services. I am looking to enhance my website and make it look more professional. Looking for very classy and Contemporary look and design for my website.

It Company

```html
<!DOCTYPE html>
<html lang="en">
<head>
<meta charset="utf-8">
<title>Beacon Advisory</title>
<link href="https://fonts.googleapis.com/css2?family=Raleway:wght@400;500;600;700&display=swap" rel="stylesheet">
<style>
:root{
  --navy:#0d3c86;
  --blue:#1f74c6;
  --blue-deep:#1a64b6;
  --cyan:#0aa6e0;
  --slate:#5f5f5f;
  --ink:#2b2b2b;
  --text:#555;
  --frame:#c9c9c9;
  --foot:#f0f0f0;
  --white:#fff;
}
*{box-sizing:border-box;margin:0;padding:0}
html,body{width:1094px;height:1200px;overflow:hidden;background:var(--white);font-family:"Raleway",Arial,sans-serif}
.page{position:relative;width:1094px;height:1200px}

.site-header{position:absolute;left:0;top:0;width:1094px;height:92px;background:var(--white);z-index:3;box-shadow:0 2px 4px rgba(0,0,0,.12)}
.brand{position:absolute;left:68px;top:22px;display:flex;align-items:center;gap:8px}
.brand-dot{width:40px;height:40px;border-radius:50%;background:var(--blue)}
.brand-name{line-height:1}
.brand-name .top{display:block;font-weight:700;font-size:21px;color:var(--navy);letter-spacing:.5px}
.brand-name .sub{display:block;font-weight:500;font-size:11px;color:#777;letter-spacing:2.6px;margin-top:2px}

.main-nav{position:absolute;left:381px;top:27px;width:646px;height:43px}
.main-nav svg{position:absolute;left:0;top:0}
.main-nav ul{position:absolute;left:0;top:0;width:646px;height:43px;list-style:none;font-size:11.5px;font-weight:600;color:var(--white);letter-spacing:.3px}
.main-nav li{position:absolute;top:15px;white-space:nowrap;line-height:14px}

.hero{position:absolute;left:0;top:92px;width:1094px;height:550px}
.hero-photo{position:absolute;inset:0;background:linear-gradient(100deg,#5d6670 0%,#c9d3dd 22%,#e9eef3 50%,#dfe6ee 75%,#f3f5f7 100%)}
.hero-cut{position:absolute;left:0;top:0}
.hero-title{position:absolute;left:68px;top:165px;font-weight:700;font-size:37px;color:var(--white);line-height:1}
.hero-title span{display:inline-block;background:rgba(70,70,70,.75);padding:4px 9px 5px 9px;margin-bottom:3px}
.dots{position:absolute;left:68px;top:278px;display:flex;gap:6px}
.dots i{width:10px;height:10px;border-radius:50%;background:var(--white)}
.dots i.on{background:#1b9ad6}

.service{position:absolute;top:450px;width:222px;height:290px;border:3px solid var(--frame);color:var(--white);text-align:center;z-index:2}
.service::after{content:"";position:absolute;left:20px;right:20px;bottom:-16px;height:8px;border-radius:50%;background:rgba(0,0,0,.12);filter:blur(3px)}
.service.consulting{left:335px;background:linear-gradient(180deg,var(--blue),var(--blue-deep))}
.service.staffing{left:570px;background:linear-gradient(180deg,#10aae2,#069ed9)}
.service.offshore{left:803px;background:linear-gradient(180deg,#666,var(--slate))}
.service .icon{display:block;width:52px;height:48px;margin:16px auto 0;border-radius:6px;background:rgba(255,255,255,.85)}
.service h3{font-weight:500;font-size:17px;line-height:21px;margin-top:14px;letter-spacing:.3px}
.service p{font-size:13px;line-height:20.3px;margin:8px 16px 0;font-weight:400}
.service .more{position:absolute;left:59px;top:235px;width:98px;height:32px;border:1.5px solid var(--white);font-size:13px;font-weight:500;line-height:29px}

.divider{position:absolute;left:68px;top:815px;width:958px;height:1px;background:#d8d8d8}
.divider-mark{position:absolute;left:530px;top:802px;width:34px;height:28px;background:var(--white)}
.divider-mark i{position:absolute;left:5px;top:1px;width:24px;height:24px;border-radius:50%;background:var(--blue)}

.welcome{position:absolute;left:68px;top:848px;width:958px;text-align:center}
.welcome h2{font-weight:500;font-size:22px;color:var(--navy);letter-spacing:.3px}
.welcome p{margin-top:12px;font-size:13.4px;line-height:22px;color:var(--text)}
.welcome .cta{position:absolute;left:410px;top:155px;width:138px;height:37px;background:linear-gradient(180deg,#3a3a3a,#111);color:var(--white);font-size:13.5px;font-weight:500;line-height:37px;border-radius:2px}

.site-footer{position:absolute;left:0;top:1074px;width:1094px;height:126px;background:var(--foot);border-top:4px solid #1893d2}
.site-footer .brand{left:68px;top:14px}
.site-footer .brand-dot{width:34px;height:34px}
.site-footer .brand-name .top{font-size:17px}
.site-footer .brand-name .sub{font-size:9px;letter-spacing:2px}
.copyright{position:absolute;left:68px;top:76px;font-size:12.5px;color:var(--ink)}
.follow{position:absolute;left:863px;top:28px;font-size:13px;color:var(--ink)}
.social{position:absolute;left:864px;top:51px;display:flex;gap:8px}
.social i{width:26px;height:26px;border-radius:50%}
</style>
</head>
<body>
<div class="page">

  <header class="site-header">
    <div class="brand">
      <span class="brand-dot"></span>
      <span class="brand-name"><span class="top">BEACON</span><span class="sub">ADVISORY</span></span>
    </div>
    <nav class="main-nav">
      <svg width="646" height="43" viewBox="0 0 646 43">
        <defs>
          <linearGradient id="navfill" x1="0" y1="0" x2="0" y2="1">
            <stop offset="0" stop-color="#1786cf"/><stop offset="1" stop-color="#0f5fae"/>
          </linearGradient>
        </defs>
        <polygon points="15,0 646,0 631,43 0,43" fill="url(#navfill)"/>
        <polygon points="15,0 82,0 82,43 0,43" fill="#0b3f8d"/>
      </svg>
      <ul>
        <li style="left:32px">HOME</li>
        <li style="left:98px">COMPANY</li>
        <li style="left:187px">SERVICES</li>
        <li style="left:273px">SOLUTIONS</li>
        <li style="left:370px">RESOURCES</li>
        <li style="left:470px">CAREER</li>
        <li style="left:547px">CONTACT US</li>
      </ul>
    </nav>
  </header>

  <section class="hero">
    <div class="hero-photo" role="img" aria-label="Photo of three smiling business consultants at a desk with a laptop in a bright office"></div>
    <svg class="hero-cut" width="1094" height="550" viewBox="0 0 1094 550">
      <polygon points="0,550 1094,392 1094,550" fill="#fff"/>
    </svg>
    <h1 class="hero-title"><span>LOREM IPSUM DOLOR SIT AMET,</span><br><span>ETUER ADIPISCING ELIT</span></h1>
    <div class="dots"><i class="on"></i><i></i><i></i><i></i></div>
  </section>

  <article class="service consulting">
    <span class="icon" role="img" aria-label="Icon of a team meeting around a table"></span>
    <h3>CONSULTING<br>SERVICES</h3>
    <p>Beacon Advisory has certified professional consultants to work with you to help increase the business by providing IT services ...</p>
    <span class="more">Read More</span>
  </article>
  <article class="service staffing">
    <span class="icon" role="img" aria-label="Icon of a group of staff members"></span>
    <h3>STAFF<br>AUGMENTATION</h3>
    <p>For years Beacon Advisory as been offering our customers the ability to augment their existing staff ..</p>
    <span class="more">Read More</span>
  </article>
  <article class="service offshore">
    <span class="icon" role="img" aria-label="Icon of a gear and wrench"></span>
    <h3>OFFSHORE<br>DEVELOPMENT</h3>
    <p>Our Offshore development model has a unique distinction of providing efficient software solutions...</p>
    <span class="more">Read More</span>
  </article>

  <div class="divider"></div>
  <div class="divider-mark"><i></i></div>

  <section class="welcome">
    <h2>WELCOME TO BEACON ADVISORY</h2>
    <p>Today’s IT market is a dynamic, fast-paced industry, with ever-increasing demands. Meeting these demands for over 25 years, Beacon Advisory maintains a global presence, aggressively recruiting expertly qualified IT and Management Professionals from around the world and cultivating key partnerships with corporations to understand their business models end-to-end, with a goal of delivering exceptional client service and ensuring a consistent delivery of the talent needed to drive results.</p>
    <span class="cta">READ MORE</span>
  </section>

  <footer class="site-footer">
    <div class="brand">
      <span class="brand-dot"></span>
      <span class="brand-name"><span class="top">BEACON</span><span class="sub">ADVISORY</span></span>
    </div>
    <div class="copyright">Copyright © 2016. All Right Reserved. Privacy Policy</div>
    <div class="follow">Follow Us:</div>
    <div class="social" aria-label="Social links">
      <i style="background:#2f5aa8"></i>
      <i style="background:#2aa3df"></i>
      <i style="background:#1a86c4"></i>
      <i style="background:#3c3c3c"></i>
      <i style="background:#f39019"></i>
    </div>
  </footer>

</div>
</body>
</html>
```